Professional Single Page Website Design for Tollbrook Advisory

Tollbrook Advisory is a new business consultancy specializing in providing expert services to small businesses, primarily in the brick-and-mortar retail and food service sectors. We offer a range of services including franchise development and launch, due diligence, and construction management.

Currently, we have a basic website set up at www.tollbrookadvisory.example, but we need a professional touch to enhance its design and functionality.

Project Requirements:
- Single Page Design: For now, we need a single page design that effectively showcases who we are, our services, and contact information.
- Future Expansion: The design should be flexible and scalable for future expansion to include additional pages like specific service offerings, about us, and a dedicated contact page.
- Design Aesthetic: We are looking for a modern yet professional design that aligns with our brand identity.
- Logo: We have a logo that we like, which was also sourced from Pixel Bazaar. The logo files are attached to this project brief.

Key Sections to Include:
- Hero Section: An engaging introduction to Tollbrook Advisory with a strong visual impact.
- About Us: A brief overview of who we are and our mission.
- Team: Section for the profiles of the two principals.
- Services: A clear and concise presentation of our services, including franchise development, due diligence, and construction management.
- Contact Information: Easy-to-find contact details, including a form for inquiries.
- Call to Action: Encouraging visitors to get in touch with us for consultations or further information.

Design Considerations:
- Ensure the design is responsive and mobile-friendly.
- Include high-quality images and icons that complement our services and industry.
- We do not need development services, this is only a design project.

```html
<!DOCTYPE html>
<html lang="en">
<head>
<meta charset="utf-8">
<title>Tollbrook Advisory</title>
<link rel="stylesheet" href="https://fonts.googleapis.com/css2?family=Poppins:wght@400;500;600;700&display=swap">
<style>
:root{
  --mint:#93c9b0;
  --mint-soft:#deede6;
  --mint-pale:#eaf4ef;
  --ink:#1f2a30;
  --slate:#2b3942;
  --slate-deep:#25323a;
  --muted:#6b7479;
  --hero-bg:#f3f3f3;
  --white:#ffffff;
}
*{margin:0;padding:0;box-sizing:border-box}
html,body{width:1200px;height:4783px;overflow:hidden}
body{font-family:"Poppins",sans-serif;color:var(--ink);background:var(--white);position:relative}
section,header,footer,.topbar{position:absolute;left:0;width:1200px}
.abs{position:absolute}
.btn{position:absolute;display:flex;align-items:center;justify-content:center;background:var(--mint);color:var(--white);border-radius:30px;font-weight:500;letter-spacing:.3px}
.accent{color:var(--mint)}

.topbar{top:0;height:37px;background:var(--mint);color:var(--white);font-size:12px}
.topbar .item{position:absolute;top:9px;display:flex;align-items:center;gap:10px}

.site-header{top:37px;height:93px;background:var(--white)}
.brand{position:absolute;display:flex;align-items:center;gap:10px}
.brand .mark{border-radius:50%;border:5px solid var(--mint)}
.brand .name{font-weight:600;line-height:1.05}
.nav{position:absolute;top:41px;font-size:14px;font-weight:500}
.nav span{position:absolute;white-space:nowrap}

.hero{top:130px;height:665px;background:var(--hero-bg)}
.hero h1{position:absolute;left:63px;top:172px;font-size:50px;line-height:56px;font-weight:700;color:var(--ink)}
.hero .tagline{position:absolute;left:63px;top:298px;font-size:16.5px;font-weight:500;color:#6fae92}
.hero .lead{position:absolute;left:63px;top:344px;width:475px;font-size:10px;line-height:13.5px;color:var(--muted)}
.hero-ring{position:absolute;left:626px;top:-47px;width:490px;height:490px;border-radius:50%;background:radial-gradient(circle,transparent 60%,#dcebe3 61%,#e8f1ec 100%)}
.hero-photo{position:absolute;left:678px;top:11px;width:438px;height:438px;border-radius:50%;background:linear-gradient(135deg,#cfd8dd 0%,#8a5a4a 45%,#3d4f5a 70%,#b7c3c8 100%)}

.services{top:795px;height:762px}
.section-title{position:absolute;left:0;width:1200px;text-align:center;font-weight:700;font-size:37px;color:var(--ink)}
.service-list{position:absolute;left:74px;top:0;font-size:16px;font-weight:600;line-height:21px;text-transform:uppercase}
.service-list div{position:absolute;left:0;width:260px}
.service-active{position:absolute;left:63px;top:312px;width:220px;height:45px;background:linear-gradient(90deg,var(--mint-soft),rgba(222,237,230,0))}
.service-panel{position:absolute;left:409px;top:234px;width:728px;height:418px;background:var(--mint-soft);padding:46px 24px 0 24px}
.service-panel h3{font-size:29px;font-weight:500;margin-bottom:18px}
.service-panel p{font-size:13.5px;line-height:23.6px;color:#555f64;margin-bottom:23px}

.about{top:1557px;height:708px;background:linear-gradient(90deg,#2a3740 0%,#33424b 60%,#3a3b3d 100%)}
.about-ring{position:absolute;left:58px;top:148px;width:422px;height:422px;border-radius:50%;background:#6f8c82}
.about-photo{position:absolute;left:76px;top:152px;width:408px;height:408px;border-radius:50%;background:linear-gradient(160deg,#9fb4c6 0%,#dfe3e4 35%,#6f8d56 65%,#4a6638 100%)}
.about h2{position:absolute;left:537px;top:200px;font-size:37px;font-weight:700;color:var(--white)}
.about h2 .ghost{color:rgba(147,201,176,.25)}
.about .copy{position:absolute;left:537px;top:275px;width:580px;font-size:12px;line-height:13.5px;color:#e4ebee}
.about .copy p{margin-bottom:11px}

.team{top:2265px;height:764px}
.team-card{position:absolute;top:251px;width:355px;height:420px;background:var(--mint-soft);text-align:center}
.team-photo{position:absolute;left:81px;top:35px;width:194px;height:194px;border-radius:50%;border:4px solid var(--mint);background:linear-gradient(180deg,#c9d3d8,#8b7566)}
.team-card .name{position:absolute;left:0;width:100%;top:256px;font-size:16px;font-weight:600}
.team-card .role{position:absolute;left:0;width:100%;top:281px;font-size:9px;color:var(--mint);letter-spacing:.5px}
.team-card .bio{position:absolute;left:22px;width:311px;top:302px;font-size:11.5px;line-height:15px;color:var(--muted)}
.team-card .icons{position:absolute;left:0;width:100%;top:383px;display:flex;justify-content:center;gap:18px}

.cta{top:3029px;height:421px;background:var(--slate)}
.cta h2{position:absolute;left:0;width:1200px;top:110px;text-align:center;font-size:36px;font-weight:700;color:var(--white)}
.cta p{position:absolute;left:140px;width:920px;top:192px;text-align:center;font-size:16px;line-height:20.5px;color:#e4ebee}

.contact{top:3450px;height:855px}
.map{position:absolute;left:84px;top:188px;width:457px;height:509px;background:linear-gradient(135deg,#f2f1ee 0%,#e7e9ea 60%,#f7e7a6 100%)}
.contact h2{position:absolute;left:615px;top:180px;font-size:37px;font-weight:700}
.field{position:absolute;border:2px solid #dfe3e5;color:#a3aaae;font-size:20px;padding:14px 22px}
.footer{top:4305px;height:478px;background:var(--slate-deep);color:var(--white)}
.footer h4{position:absolute;font-size:28px;font-weight:400;color:var(--mint)}
.footer ul{position:absolute;list-style:none;font-size:16px}
.footer li{height:43px;display:flex;align-items:center;gap:12px}
.footer li::before{content:"";width:16px;height:3px;background:var(--white)}
.info{position:absolute;left:961px;display:flex;gap:14px;align-items:center}
.info .lbl{font-size:9px;color:var(--mint);font-weight:500}
.info .val{font-size:11px;color:#d9e1e4}
.socials{position:absolute;top:4px}
.footer .rule{position:absolute;left:92px;width:1035px;top:424px;height:1px;background:#44525a}
.footer .copy{position:absolute;left:0;width:1200px;top:440px;text-align:center;font-size:14px;color:#d9e1e4}
</style>
</head>
<body>

<div class="topbar">
  <div class="item" style="left:60px">
    <svg width="20" height="20" viewBox="0 0 24 24" fill="none" stroke="#fff" stroke-width="1.6"><path d="M5 3h4l2 5-3 2a11 11 0 0 0 6 6l2-3 5 2v4a2 2 0 0 1-2 2A17 17 0 0 1 3 5a2 2 0 0 1 2-2z"/></svg>
    <span>+1 555 014 2290</span>
  </div>
  <div class="item" style="left:293px">
    <svg width="22" height="20" viewBox="0 0 24 24" fill="none" stroke="#fff" stroke-width="1.6"><rect x="3" y="6" width="18" height="13" rx="1"/><path d="M3 7l9 7 9-7"/></svg>
    <span>hello@tollbrookadvisory.example</span>
  </div>
</div>

<header class="site-header">
  <div class="brand" style="left:50px;top:17px">
    <div class="mark" style="width:62px;height:62px"></div>
    <div class="name" style="font-size:18px;color:var(--ink)">Tollbrook<br>Advisory</div>
  </div>
  <nav class="nav">
    <span style="left:377px">HOME</span>
    <span style="left:481px">ABOUT</span>
    <span style="left:595px">SERVICE</span>
    <span style="left:719px">TEAM</span>
  </nav>
  <div class="btn" style="left:994px;top:32px;width:143px;height:36px;font-size:13px">CONTACT</div>
</header>

<section class="hero">
  <h1>Building Success in<br>Southern California</h1>
  <div class="tagline">Expertise at Every Step: From Planning to Execution</div>
  <p class="lead">At Tollbrook, we blend innovative strategies with local market expertise to guide your commercial real estate ventures. Whether you're launching a new restaurant, investing in retail spaces, or expanding a franchise, our dedicated team is here to turn your real estate aspirations into tangible success. Dive into a partnership that grows with you.</p>
  <div class="btn" style="left:63px;top:457px;width:156px;height:39px;font-size:14px">LEARN MORE</div>
  <div class="hero-ring"></div>
  <div class="hero-photo" role="img" aria-label="Modern retail storefront with brick and blue steel facade"></div>
</section>

<section class="services">
  <h2 class="section-title" style="top:105px">TOLLBROOK <span class="accent">SERVICES</span></h2>
  <div class="service-active"></div>
  <div class="service-list">
    <div style="top:237px">Franchise Development<br>&amp; Launch</div>
    <div style="top:323px">Due Diligence</div>
    <div style="top:397px">Building &amp; Construction<br>Management</div>
    <div style="top:490px">Market Analysis &amp;<br>Feasibility Studies</div>
    <div style="top:588px">Investment Property<br>Evaluation</div>
  </div>
  <div class="service-panel">
    <h3>Due Diligence Services</h3>
    <p>Tollbrook offers comprehensive evaluations tailored to your business needs. We meticulously assess franchise opportunities, business sales, and property transactions, identifying potential risks and liabilities to safeguard your investments. Our expert team provides actionable recommendations on deal points and offers strategic guidance throughout the entire process.</p>
    <p>Whether you're exploring new ventures or expanding your portfolio, trust us to deliver detailed insights and informed advice, ensuring you make confident, well-informed decisions. Partner with us for thorough due diligence that supports your success and minimizes uncertainties in any deal.</p>
  </div>
</section>

<section class="about">
  <div class="about-ring"></div>
  <div class="about-photo" role="img" aria-label="Aerial view of a modern office building surrounded by trees"></div>
  <h2>ABOUT <span class="accent">TOLLBROOK</span> <span class="ghost">ADVISORY</span></h2>
  <div class="copy">
    <p>Welcome to Tollbrook Advisory, your trusted partner in navigating the complexities of the real estate and small business markets. Founded by industry veterans Daniel Reyes and Kevin Lau, we specialize in providing comprehensive services tailored to the unique needs of our clients. Whether you're a franchisee, a new restaurant owner, or a commercial real estate investor, our expertise in due diligence, construction management, and investment property evaluation ensures you make informed, strategic decisions.</p>
    <p>At Tollbrook Advisory, we are committed to your success. Our approach combines meticulous analysis, strategic insights, and personalized service to help you achieve your business goals. We pride ourselves on our ability to deliver results that exceed expectations, fostering long-term relationships built on trust and excellence.</p>
    <p>Discover how Tollbrook Advisory can support your business journey. Partner with us and experience the difference our dedication and expertise can make.</p>
  </div>
  <div class="btn" style="left:531px;top:518px;width:156px;height:39px;font-size:14px">LEARN MORE</div>
</section>

<section class="team">
  <h2 class="section-title" style="top:112px">OUR <span class="accent">LEADERSHIP</span> TEAM</h2>
  <div class="team-card" style="left:193px">
    <div class="team-photo" role="img" aria-label="Portrait of principal Daniel Reyes"></div>
    <div class="name">Daniel Reyes</div>
    <div class="role">PRINCIPAL</div>
    <div class="bio">Daniel Reyes brings almost 20 years of rich experience as a real estate investor and a pivotal role at one of southern California's largest real estate management firms, where he...</div>
    <div class="icons">
      <svg width="24" height="24" viewBox="0 0 24 24" fill="#93c9b0"><path d="M5 2h4l2 5-3 2a12 12 0 0 0 7 7l2-3 5 2v4a2 2 0 0 1-2 2A18 18 0 0 1 3 4a2 2 0 0 1 2-2z"/></svg>
      <svg width="26" height="24" viewBox="0 0 26 24" fill="#93c9b0"><path d="M2 9l11-7 11 7v12H2z"/><path d="M2 9l11 7 11-7" stroke="#deede6" stroke-width="1.5" fill="none"/></svg>
    </div>
  </div>
  <div class="team-card" style="left:648px">
    <div class="team-photo" role="img" aria-label="Portrait of principal Kevin Lau"></div>
    <div class="name">Kevin Lau</div>
    <div class="role">PRINCIPAL</div>
    <div class="bio">Kevin Lau brings almost 20 years of rich experience as a real estate investor and a pivotal role at one of southern California's largest real estate management firms, where he...</div>
    <div class="icons">
      <svg width="24" height="24" viewBox="0 0 24 24" fill="#93c9b0"><path d="M5 2h4l2 5-3 2a12 12 0 0 0 7 7l2-3 5 2v4a2 2 0 0 1-2 2A18 18 0 0 1 3 4a2 2 0 0 1 2-2z"/></svg>
      <svg width="26" height="24" viewBox="0 0 26 24" fill="#93c9b0"><path d="M2 9l11-7 11 7v12H2z"/><path d="M2 9l11 7 11-7" stroke="#deede6" stroke-width="1.5" fill="none"/></svg>
    </div>
  </div>
</section>

<section class="cta">
  <h2>UNLOCK YOUR <span class="accent">BUSINESS POTENTIAL</span> TODAY!</h2>
  <p>At Tollbrook Advisory, we're dedicated to turning your business aspirations into reality. Our expertise and commitment ensure you make informed, strategic decisions that drive success. Take the first step towards achieving your goals with confidence.</p>
  <div class="btn" style="left:552px;top:276px;width:154px;height:36px;font-size:14px">LEARN MORE</div>
</section>

<section class="contact">
  <div class="map" role="img" aria-label="Street map showing the office location, Suite 100"></div>
  <h2><span class="accent">CONTACT</span> US</h2>
  <div class="field" style="left:615px;top:264px;width:240px;height:58px">Name</div>
  <div class="field" style="left:879px;top:264px;width:239px;height:58px">Email</div>
  <div class="field" style="left:615px;top:346px;width:240px;height:57px">Phone</div>
  <div class="field" style="left:879px;top:346px;width:239px;height:57px">Company</div>
  <div class="field" style="left:615px;top:430px;width:503px;height:163px;padding-top:26px">Additional Message</div>
  <div class="btn" style="left:760px;top:648px;width:188px;height:49px;font-size:18px">SEND NOW</div>
</section>

<footer class="footer">
  <div class="brand" style="left:69px;top:117px">
    <div class="mark" style="width:88px;height:88px;border-width:6px"></div>
    <div class="name" style="font-size:27px;color:var(--white)">Tollbrook<br>Advisory</div>
  </div>
  <svg class="socials" style="left:90px;top:253px" width="170" height="28" viewBox="0 0 170 28" fill="none" stroke="#93c9b0" stroke-width="2.5">
    <circle cx="12" cy="14" r="10"/><circle cx="79" cy="14" r="10"/><circle cx="150" cy="14" r="10"/>
  </svg>
  <h4 style="left:418px;top:128px">Quick Links</h4>
  <ul style="left:436px;top:189px"><li>Home</li><li>About</li><li>Services</li><li>Contact</li></ul>
  <h4 style="left:700px;top:130px">Services</h4>
  <ul style="left:700px;top:191px"><li>Home</li><li>About</li><li>Services</li><li>Contact</li></ul>
  <h4 style="left:961px;top:133px">Contact Info</h4>
  <div class="info" style="top:196px">
    <svg width="38" height="40" viewBox="0 0 38 40" fill="none" stroke="#fff" stroke-width="1.6"><path d="M19 4a9 9 0 0 1 9 9c0 7-9 16-9 16s-9-9-9-16a9 9 0 0 1 9-9z"/><circle cx="19" cy="13" r="3.5"/><path d="M8 30l-5 7h32l-5-7"/></svg>
    <div><div class="lbl">OUR ADDRESS</div><div class="val">United States</div></div>
  </div>
  <div class="info" style="top:262px">
    <svg width="38" height="40" viewBox="0 0 38 40" fill="none" stroke="#fff" stroke-width="1.6"><path d="M10 4h7l3 8-4 3a16 16 0 0 0 8 8l3-4 8 3v7a3 3 0 0 1-3 3A27 27 0 0 1 7 7a3 3 0 0 1 3-3z"/></svg>
    <div><div class="lbl">CALL US NOW</div><div class="val">+1 555 014 2290</div></div>
  </div>
  <div class="info" style="top:330px">
    <svg width="38" height="40" viewBox="0 0 38 40" fill="none" stroke="#fff" stroke-width="1.6"><path d="M4 15l15-10 15 10v20H4z"/><path d="M4 15l15 11 15-11"/></svg>
    <div><div class="lbl">SEND AN EMAIL</div><div class="val">hello@tollbrookadvisory.example</div></div>
  </div>
  <div class="rule"></div>
  <div class="copy">Copyright © 2024 Tollbrook Advisory. All Rights Reserved.</div>
</footer>

</body>
</html>
```